Web design for business website

I need a web design for a business website for one of our clients who is specialized in alarm management software. I would like you to design 3 web pages, one for each of the 3 pages. You need to process the corporate identity of our client to the web design. This means the colors of the logo (red and black) should definitely show up on all of the 3 pages. Find the logo file for the logo of our customer. To increase readability I suggest you use a white/light background. All suggestions are welcome.

Please kindly download atttached Webdesign.zip and read the project brief first. The project brief refers to all other files of the zip file. Your design must have exactly the same structure as the wireframes.
Updates

Target Market(s)

B2B, Alarm management

Industry/Entity Type

Business

Number of Pages Required

3 page

Requirements
Must have
• The web design must have exactly the same structure as the wireframes and needs to contain the colors of the company logo.

```html
<!DOCTYPE html>
<html lang="en">
<head>
<meta charset="utf-8">
<title>Kaltrix – Real-time reasoning solutions</title>
<link rel="stylesheet" href="https://fonts.googleapis.com/css2?family=Open+Sans:wght@400;600&family=Raleway:wght@400;500;600;700&display=swap">
<style>
:root{
  --accent:#e8461b;
  --dark:#151515;
  --navy:#16162b;
  --topbar:#1a1a1a;
  --header:#ececec;
  --text:#666;
  --light-line:#dcdcdc;
  --white:#fff;
}
*{box-sizing:border-box;margin:0;padding:0}
html,body{width:753px;height:1200px;overflow:hidden}
body{font-family:'Open Sans',sans-serif;background:var(--white);color:var(--text);position:relative}
.wrap{position:absolute;left:62px;width:629px}
a{color:inherit;text-decoration:none}

.topbar{position:absolute;top:0;left:0;width:753px;height:21px;background:var(--topbar);color:#aaa;font-size:7px}
.topbar .phone{position:absolute;left:62px;top:6px;display:flex;gap:5px;align-items:center}
.topbar .tools{position:absolute;right:63px;top:0;height:21px;display:flex;border-left:1px solid #333}
.topbar .tools span{display:flex;align-items:center;justify-content:center;height:21px;padding:0 9px;border-right:1px solid #333}

.header{position:absolute;top:21px;left:0;width:753px;height:54px;background:var(--header)}
.brand{position:absolute;left:62px;top:15px}
.brand-name{font-family:'Raleway',sans-serif;font-weight:600;font-size:18px;color:#333;line-height:18px;letter-spacing:.5px}
.brand-tag{font-family:'Raleway',sans-serif;font-size:6.5px;color:#555;margin-top:2px}
.header-actions{position:absolute;right:62px;top:14px;display:flex;gap:5px}
.header-actions span{width:43px;height:27px;background:var(--accent);border:1px solid #c43810;display:flex;align-items:center;justify-content:center}

.nav{position:absolute;top:75px;left:0;width:753px;height:27px;background:var(--navy)}
.nav ul{list-style:none;position:absolute;left:62px;top:3px;display:flex;font-family:'Open Sans',sans-serif;font-size:7.5px;color:#ddd}
.nav li{height:21px;display:flex;align-items:center;padding:0 15px;margin-right:9px}
.nav li.active{background:var(--accent);color:#fff;font-weight:600}

.hero{position:absolute;top:102px;left:0;width:753px;height:269px;background:linear-gradient(160deg,#1c2a4a 0%,#6b6a4a 40%,#a88d3f 60%,#3a4b5c 100%)}
.hero-title{position:absolute;left:62px;top:82px;background:rgba(255,255,255,.92);padding:3px 12px;display:flex;align-items:baseline;gap:6px}
.hero-title b{font-family:'Raleway',sans-serif;font-weight:700;font-size:30px;color:var(--accent)}
.hero-title span{font-family:'Raleway',sans-serif;font-size:13px;color:#222}
.hero-caption{position:absolute;left:62px;top:128px;width:361px;height:25px;background:rgba(22,22,43,.9);color:#fff;font-size:8px;padding:6px 11px}
.hero-arrows{position:absolute;left:62px;top:156px;display:flex;gap:5px}
.hero-arrows span{width:32px;height:32px;display:flex;align-items:center;justify-content:center}
.hero-arrows .prev{background:#e8e8e8}
.hero-arrows .next{background:var(--accent)}

.welcome{position:absolute;top:371px;left:0;width:753px;height:269px;background:var(--dark);color:#ddd}
.welcome h1{position:absolute;left:62px;top:36px;font-family:'Raleway',sans-serif;font-weight:400;font-size:22px;color:#fff;display:flex;align-items:baseline;gap:7px;white-space:nowrap}
.welcome h1 b{font-family:'Raleway',sans-serif;font-weight:700;font-size:32px;color:var(--accent)}
.welcome h1 small{font-size:13px}
.welcome .copy{position:absolute;left:62px;top:89px;width:518px;font-size:7.2px;line-height:10.8px}
.welcome .copy p+p{margin-top:10px}
.btn-outline{position:absolute;left:62px;top:200px;width:87px;height:27px;border:1.5px solid var(--accent);color:var(--accent);font-size:7px;font-weight:600;display:flex;align-items:center;justify-content:center}

.clients-head{position:absolute;top:678px}
.clients-head h2{font-family:'Raleway',sans-serif;font-weight:600;font-size:21px;color:var(--accent)}
.clients-head p{font-size:8px;color:#777;margin-top:2px}
.clients{position:absolute;top:743px;left:0;width:753px;height:55px;border-top:1px solid var(--light-line);border-bottom:1px solid var(--light-line)}
.clients ul{list-style:none;position:absolute;left:84px;right:70px;top:0;height:53px;display:flex;justify-content:space-between;align-items:center;font-family:'Raleway',sans-serif;font-weight:600;font-size:11px;color:#555}
.clients li{display:flex;align-items:center;gap:4px}
.clients li i{width:10px;height:10px;border-radius:50%;background:#bbb;display:block}

.social{position:absolute;top:850px;left:0;width:753px;height:135px;background:linear-gradient(180deg,#0d0d10,#1b1b1f)}
.social h3{font-family:'Raleway',sans-serif;font-weight:500;font-size:19px;color:var(--accent);position:absolute;top:35px}
.follow{left:62px}
.subscribe{left:276px}
.social-links{position:absolute;left:62px;top:70px;display:flex;gap:6px}
.social-links span{width:27px;height:27px;background:#555}
.social-links span:first-child{background:#3b5998}
.sub-form{position:absolute;left:277px;top:70px;width:414px;height:27px;border:1px solid #fff;display:flex}
.sub-form .field{flex:1;color:#fff;font-size:7.5px;display:flex;align-items:center;padding-left:15px}
.sub-form .go{width:75px;background:#fff;color:var(--accent);font-size:7px;font-weight:600;display:flex;align-items:center;justify-content:center}

.footer{position:absolute;top:1026px;left:62px;width:629px;font-size:7.5px;color:#888}
.col{position:absolute;top:0}
.col h4{font-family:'Raleway',sans-serif;font-weight:500;font-size:10px;color:#333;margin-bottom:10px}
.col li{list-style:none;line-height:12px}
.col li.hl{color:var(--accent)}
.contact li{display:flex;gap:9px;align-items:center;line-height:17.5px}
.rule{position:absolute;top:1167px;left:0;width:753px;border-top:1px solid var(--light-line)}
.copyright{position:absolute;top:1177px;left:0;width:753px;text-align:center;font-size:6px;color:#888}
.copyright span{color:var(--accent)}
</style>
</head>
<body>

<div class="topbar">
  <div class="phone">
    <svg width="7" height="7" viewBox="0 0 10 10"><path d="M2 0l2 2-1 2c1 1 2 2 3 3l2-1 2 2-1 2C4 10 0 6 0 1z" fill="#888"/></svg>
    +31 (0)20 555 0148
  </div>
  <div class="tools">
    <span><svg width="6" height="4" viewBox="0 0 6 4"><path d="M0 0h6L3 4z" fill="#aaa"/></svg></span>
    <span>ENG</span>
    <span><svg width="7" height="7" viewBox="0 0 10 10"><circle cx="4" cy="4" r="3" stroke="#aaa" stroke-width="1.5" fill="none"/><path d="M6 6l3 3" stroke="#aaa" stroke-width="1.5"/></svg></span>
  </div>
</div>

<header class="header">
  <div class="brand">
    <div class="brand-name">Kaltrix</div>
    <div class="brand-tag">Real-time reasoning solutions</div>
  </div>
  <div class="header-actions">
    <span><svg width="7" height="7" viewBox="0 0 10 10"><circle cx="5" cy="3" r="2.5" fill="#fff"/><path d="M0 10c0-3 2-4 5-4s5 1 5 4z" fill="#fff"/></svg></span>
    <span><svg width="8" height="7" viewBox="0 0 10 9"><rect x="0" y="4" width="6" height="5" fill="#fff"/><path d="M4 4V2a2 2 0 014 0v1" stroke="#fff" stroke-width="1.4" fill="none"/></svg></span>
    <span><svg width="8" height="7" viewBox="0 0 10 9"><path d="M0 3h4V1l4 3.5L4 8V6H0z" fill="#fff"/><path d="M7 1h2v7H7" stroke="#fff" fill="none"/></svg></span>
  </div>
</header>

<nav class="nav">
  <ul>
    <li class="active">HOME</li><li>INDUSTRY</li><li>TELECOM</li><li>POWER</li><li>UTILITIES</li><li>INFRA</li><li>STORE</li>
  </ul>
</nav>

<section class="hero" role="img" aria-label="Photograph of an industrial refinery lit up at dusk">
  <div class="hero-title"><b>KALTRIX</b><span>Real-time reasoning solutions</span></div>
  <div class="hero-caption">Companies have invested to get data out of processes...</div>
  <div class="hero-arrows">
    <span class="prev"><svg width="5" height="7" viewBox="0 0 5 8"><path d="M4 1L1 4l3 3" stroke="var(--accent)" stroke-width="1.5" fill="none"/></svg></span>
    <span class="next"><svg width="5" height="7" viewBox="0 0 5 8"><path d="M1 1l3 3-3 3" stroke="#fff" stroke-width="1.5" fill="none"/></svg></span>
  </div>
</section>

<section class="welcome">
  <h1>Welcome to <b>KALTRIX</b> <small>Real-time reasoning solutions</small></h1>
  <div class="copy">
    <p>Companies have invested to get data out of processes. New technologies have been developed to get real-time data out of the harshest places, like oil-well drill heads or the Great Barrier Riff. Data in itself means nothing without the context the data is collected in. Example: data from equipment under maintenance does not provide information to operations. Information - data which is valid and meaningful can overwhelm any user without the proper knowledge to interpret this information.</p>
    <p>Kaltrix technology enables easy application of such knowledge in a comprehensible – visual – representation and makes hypothetical reasoning with information possible providing meaningful advisories to subscribers when they need it or when it is required that they are made aware of a situation which requires their attention.</p>
  </div>
  <a class="btn-outline" href="#">LEARN MORE</a>
</section>

<div class="wrap clients-head">
  <h2>OUR CLIENTS</h2>
  <p>Some of our clients that trust us, be shure to be one of them.</p>
</div>
<section class="clients">
  <ul>
    <li>Norvane</li>
    <li>Petrowell</li>
    <li><i></i>Solmar</li>
    <li><i></i>Quadrix</li>
    <li>Brouwstad</li>
    <li>Coralis</li>
    <li>Tidemark Oil</li>
  </ul>
</section>

<section class="social">
  <h3 class="follow">FOLLOW US ON :</h3>
  <h3 class="subscribe">SUBSCRIBE NOW :</h3>
  <div class="social-links">
    <span aria-label="Social link 1"></span><span aria-label="Social link 2"></span><span aria-label="Social link 3"></span><span aria-label="Social link 4"></span><span aria-label="Social link 5"></span>
  </div>
  <div class="sub-form">
    <div class="field">Enter Your Email Adress</div>
    <div class="go">SUBSCRIBE</div>
  </div>
</section>

<footer class="footer">
  <div class="col" style="left:0">
    <h4>SOLUTIONS</h4>
    <ul><li class="hl">ALM Alarm Reporting</li><li>ALM Alarm Analysis</li><li>ALM Alarm Expert</li><li>USE</li></ul>
  </div>
  <div class="col" style="left:107px">
    <h4>INDUSTRIES</h4>
    <ul><li>Industry</li><li>Telecom</li><li>Power</li><li>Utilites</li><li>Infra</li></ul>
  </div>
  <div class="col" style="left:215px">
    <h4>ABOUT US</h4>
    <ul><li>Company</li><li>Overview</li><li>Leadership</li><li>Partners</li><li>Locations</li></ul>
  </div>
  <div class="col" style="left:322px">
    <h4>NEWS</h4>
    <ul><li>Product News</li><li>Partner News</li><li>Events</li><li>Press Releases</li><li>Vacancies</li></ul>
  </div>
  <div class="col contact" style="left:484px">
    <h4>CONTACT US</h4>
    <ul>
      <li><svg width="7" height="7" viewBox="0 0 10 10"><path d="M2 0l2 2-1 2c1 1 2 2 3 3l2-1 2 2-1 2C4 10 0 6 0 1z" fill="#888"/></svg>+31 (0)20 555 0148</li>
      <li><svg width="8" height="6" viewBox="0 0 10 7"><rect width="10" height="7" fill="#888"/><path d="M0 0l5 4 5-4" stroke="#fff" fill="none"/></svg>info@kaltrix.example</li>
      <li><svg width="6" height="8" viewBox="0 0 8 11"><path d="M4 0a4 4 0 014 4c0 3-4 7-4 7S0 7 0 4a4 4 0 014-4z" fill="#888"/><circle cx="4" cy="4" r="1.5" fill="#fff"/></svg>Havenweg 12, Kaltrix</li>
    </ul>
  </div>
</footer>
<div class="rule"></div>
<div class="copyright">Copyright © 2105 <span>KALTRIX</span>. All Rights Reserved.</div>

</body>
</html>
```